Local Flower Farm Needs Business Card Design

I need business cards designed for a flower farm based in Eudora, Kansas.
Business Info:
We are a local cut flower farm located in Eudora, Kansas, founded by Corinne Haldwick. What started as a passion for agriculture and search for more joy in daily life has blossomed into a small business dedicated to providing the community with beautiful, fresh, and sustainable flowers. We specialize in local, seasonal blooms, ensuring that every petal reflects the care and dedication we pour into our craft. Our mission is to deliver the highest quality flowers directly to our customers through local farmers markets and to florists who share our commitment to sustainability. Join us in celebrating the beauty of nature, one bloom at a time!
Contact Details:
Corinne Haldwick
Owner
Phone 913-555-0147
Facebook: Rosalind Thorpe Gardens
Instagram: @RosalindThorpeGardens
Website: RosalindThorpeGardens.example
Target Market(s)
Wholesale to Florists and Direct to Consumer via Farmers Market
Industry/Entity Type
Florist, Farm
Contact Information for Business Card
Name, Contact Info, Logo
Look and feel
Each slider illustrates characteristics of the customer's brand and the style your logo design should communicate.

```html
<!DOCTYPE html>
<html lang="en">
<head>
<meta charset="utf-8">
<title>Rosalind Thorpe Gardens – Business Card</title>
<link href="https://fonts.googleapis.com/css2?family=Tinos&family=Mulish:wght@400;500&display=swap" rel="stylesheet">
<style>
  :root{
    --bg:#3b3b3d;
    --teal-deep:#0c262c;
    --teal:#0f3037;
    --teal-light:#1b6e7c;
    --paper:#ffffff;
    --ink:#10343a;
    --rule:#c9cfd0;
  }
  *{box-sizing:border-box;margin:0;padding:0}
  html,body{width:1200px;height:689px;overflow:hidden;background:var(--bg)}
  .stage{position:relative;width:1200px;height:689px}
  .card{position:absolute;top:190px;width:540px;height:309px;border-radius:22px;overflow:hidden;box-shadow:0 14px 30px rgba(0,0,0,.45)}
  .card--front{left:36px;background:linear-gradient(160deg,var(--teal) 0%,var(--teal-deep) 100%)}
  .card--back{left:624px;background:var(--paper)}

  /* front */
  .front-decoration{position:absolute;left:0;top:0;width:270px;height:309px;
    background:linear-gradient(200deg,rgba(27,110,124,.85) 0%,rgba(19,72,82,.55) 45%,rgba(12,38,44,0) 100%)}
  .front-name{position:absolute;left:270px;right:24px;top:112px;text-align:center;
    font-family:"Tinos",serif;color:var(--paper);font-size:25px;letter-spacing:1.5px;line-height:1.25}

  /* back */
  .brand-mark{position:absolute;left:38px;top:62px;width:170px;height:170px;border:1.5px solid var(--ink);border-radius:50%;
    display:flex;align-items:center;justify-content:center;text-align:center}
  .brand-mark__name{font-family:"Tinos",serif;color:var(--ink);font-size:19px;line-height:1.2;letter-spacing:1px;text-transform:uppercase}
  .divider{position:absolute;left:0;top:0}
  .contact{position:absolute;left:262px;top:44px;color:var(--ink)}
  .contact__name{font-family:"Tinos",serif;font-size:21px;letter-spacing:1px;text-transform:uppercase}
  .contact__role{font-family:"Mulish",sans-serif;font-size:14px;margin-top:2px}
  .contact__list{list-style:none;margin-top:18px}
  .contact__item{display:flex;align-items:center;gap:8px;font-family:"Mulish",sans-serif;font-size:13.5px;font-weight:500;margin-bottom:6px}
  .icon{width:18px;height:18px;flex:none}
  .band{position:absolute;left:0;right:0;bottom:0;height:42px;background:var(--teal)}
  .band-rule{position:absolute;left:0;right:0;bottom:48px;height:1.5px;background:var(--teal)}
  .seal{position:absolute;right:26px;bottom:22px;width:46px;height:46px;border-radius:50%;background:var(--paper);border:1.5px solid var(--teal)}
</style>
</head>
<body>
<main class="stage">
  <section class="card card--front" aria-label="Card front">
    <div class="front-decoration" role="img" aria-label="Large floral monogram decoration in teal tones"></div>
    <h1 class="front-name">ROSALIND THORPE<br>GARDENS</h1>
  </section>

  <section class="card card--back" aria-label="Card back">
    <div class="brand-mark"><span class="brand-mark__name">Rosalind<br>Thorpe<br>Gardens</span></div>
    <svg class="divider" width="540" height="309" aria-hidden="true"><line x1="240" y1="30" x2="240" y2="240" stroke="var(--rule)" stroke-width="1"/></svg>
    <div class="contact">
      <h2 class="contact__name">Corinne Haldwick</h2>
      <p class="contact__role">Owner</p>
      <ul class="contact__list">
        <li class="contact__item">
          <svg class="icon" viewBox="0 0 18 18" aria-hidden="true"><circle cx="9" cy="9" r="8.2" fill="none" stroke="var(--ink)" stroke-width="1"/><path d="M6 5.2l1.6-.4.9 2-1 .8a5 5 0 0 0 2.9 2.9l.8-1 2 .9-.4 1.6c-3.7.3-7.1-3.1-6.8-6.8z" fill="var(--ink)"/></svg>
          913-555-0147</li>
        <li class="contact__item">
          <svg class="icon" viewBox="0 0 18 18" aria-hidden="true"><circle cx="9" cy="9" r="8.2" fill="none" stroke="var(--ink)" stroke-width="1"/></svg>
          Rosalind Thorpe Gardens</li>
        <li class="contact__item">
          <svg class="icon" viewBox="0 0 18 18" aria-hidden="true"><circle cx="9" cy="9" r="8.2" fill="none" stroke="var(--ink)" stroke-width="1"/></svg>
          @RosalindThorpeGardens</li>
        <li class="contact__item">
          <svg class="icon" viewBox="0 0 18 18" aria-hidden="true"><circle cx="9" cy="9" r="8.2" fill="none" stroke="var(--ink)" stroke-width="1"/><circle cx="9" cy="9" r="4.6" fill="none" stroke="var(--ink)" stroke-width="1"/><ellipse cx="9" cy="9" rx="2" ry="4.6" fill="none" stroke="var(--ink)" stroke-width="1"/><line x1="4.4" y1="9" x2="13.6" y2="9" stroke="var(--ink)" stroke-width="1"/></svg>
          RosalindThorpeGardens.example</li>
      </ul>
    </div>
    <div class="band-rule"></div>
    <div class="band"></div>
    <div class="seal" aria-hidden="true"></div>
  </section>
</main>
</body>
</html>
```